Harborline Renewal Business Card Design

Professional and clean design. The design colors should flow with the logo. Two-sided card with the website on the back which is:

www.HarborlineRenewal.example.

"Specializing in Water Damage Restoration"

On the front I need the name, email, phone, and logo.

Name: Darnell Quisby
Email: Darnell@HarborlineRenewal.example
Phone: 555-318-2046 for now

I only have the Preview and Thumbnail right now but should have the source files uploaded within a day or two.

Target Market(s)

Flood victims, home owners with water damage from busted pipes etc...

Industry/Entity Type

Business

Contact Information for Business Card

Name: Darnell Quisby

Font styles to use
Serif
Sans Serif

Requirements
Must have
• Business Card Details Info

```html
<!DOCTYPE html>
<html lang="en">
<head>
<meta charset="utf-8">
<title>Harborline Renewal Business Card</title>
<link rel="stylesheet" href="https://fonts.googleapis.com/css2?family=Cinzel:wght@400;600&family=Open+Sans:wght@400;600&display=swap">
<style>
  :root {
    --page: #e9e7e4;
    --paper: #ffffff;
    --brand: #3aa6dc;
    --brand-deep: #1d82c6;
    --brand-light: #62c3ea;
    --wave: #8fd6f1;
    --ink-white: #ffffff;
    --shadow: rgba(40, 50, 60, 0.18);
  }
  * { box-sizing: border-box; margin: 0; padding: 0; }
  html, body { width: 1200px; height: 800px; overflow: hidden; }
  body {
    background: var(--page);
    display: flex;
    align-items: center;
    justify-content: center;
    gap: 40px;
  }
  .card {
    position: relative;
    width: 540px;
    height: 309px;
    border-radius: 4px;
    box-shadow: 0 10px 28px var(--shadow);
    overflow: hidden;
  }

  /* Back side */
  .card-back {
    background: var(--paper);
    display: flex;
    flex-direction: column;
    align-items: center;
    justify-content: center;
    color: var(--brand);
  }
  .brand-lockup {
    display: flex;
    align-items: center;
    gap: 22px;
  }
  .brand-name {
    font-family: "Cinzel", serif;
    font-weight: 400;
    font-size: 34px;
    line-height: 1.15;
    letter-spacing: 2px;
    text-align: center;
    color: var(--brand);
  }
  .brand-name .line-2 {
    display: block;
    font-size: 17px;
    letter-spacing: 7px;
  }
  .brand-dot {
    width: 58px;
    height: 58px;
    border-radius: 50%;
    background: var(--brand);
    flex-shrink: 0;
  }
  .tagline {
    margin-top: 28px;
    font-family: "Open Sans", sans-serif;
    font-size: 14px;
    color: var(--brand-deep);
  }
  .website {
    margin-top: 6px;
    font-family: "Open Sans", sans-serif;
    font-size: 13px;
    color: var(--brand);
  }

  /* Front side */
  .card-front {
    background: linear-gradient(150deg, var(--brand-light) 0%, var(--brand) 45%, var(--brand-deep) 100%);
    color: var(--ink-white);
  }
  .front-wave {
    position: absolute;
    inset: 0;
    width: 100%;
    height: 100%;
  }
  .person {
    position: absolute;
    top: 26px;
    left: 30px;
  }
  .person-name {
    font-family: "Cinzel", serif;
    font-size: 20px;
    letter-spacing: 1.5px;
  }
  .person-role {
    margin-top: 4px;
    font-family: "Open Sans", sans-serif;
    font-size: 9px;
    letter-spacing: 1.5px;
    opacity: 0.85;
  }
  .front-brand {
    position: absolute;
    top: 118px;
    left: 0;
    right: 0;
    display: flex;
    align-items: center;
    justify-content: center;
    gap: 14px;
  }
  .front-brand .brand-ring {
    width: 46px;
    height: 46px;
    border-radius: 50%;
    border: 4px solid var(--ink-white);
  }
  .front-brand .brand-name {
    color: var(--ink-white);
    font-size: 24px;
  }
  .contact {
    position: absolute;
    right: 30px;
    bottom: 24px;
    text-align: right;
    font-family: "Open Sans", sans-serif;
    font-size: 14px;
    line-height: 1.6;
  }
</style>
</head>
<body>

  <section class="card card-back">
    <div class="brand-lockup">
      <div class="brand-name">Harborline<span class="line-2">Renewal</span></div>
      <div class="brand-dot"></div>
    </div>
    <p class="tagline">"Specializing in Water Damage Restoration"</p>
    <p class="website">www.HarborlineRenewal.example</p>
  </section>

  <section class="card card-front">
    <svg class="front-wave" viewBox="0 0 540 309" preserveAspectRatio="none" aria-hidden="true">
      <path d="M0 110 C 140 110, 200 190, 320 185 C 420 180, 480 150, 540 140 L540 309 L0 309 Z" fill="var(--wave)" opacity="0.55"/>
    </svg>
    <div class="person">
      <div class="person-name">Darnell Quisby</div>
      <div class="person-role">REALTOR</div>
    </div>
    <div class="front-brand">
      <div class="brand-ring"></div>
      <div class="brand-name">Harborline Renewal</div>
    </div>
    <div class="contact">
      <div class="phone">555-318-2046</div>
      <div class="email">Darnell@HarborlineRenewal.example</div>
    </div>
  </section>

</body>
</html>
```